Vigil Ledger Suite (Web Design)

Design with your logo. Background in black or dark. Elegant style, it's a website for professional people only. Our company provides a cloud software manager for Funeral Services Companies.

Target Market(s)

Professional of Funeral Services.

Coding

Coded - Design and coding required

Number of Pages Required

3 page

Font styles to use
Sans Serif

Colors
fbee3d
000000
5c5c5c

Requirements
Must have
• Design of the website should be similar to our logo colors.

```html
<!DOCTYPE html>
<html lang="en">
<head>
<meta charset="utf-8">
<title>Vigil Ledger Suite — Funeral Management Software</title>
<link rel="stylesheet" href="https://fonts.googleapis.com/css2?family=Exo+2:wght@600;700;800&family=Open+Sans:ital,wght@0,400;0,600;0,700;1,400&display=swap">
<style>
:root{
  --yellow:#fbee3d;
  --black:#000000;
  --ink:#1e1e1e;
  --grey:#5c5c5c;
  --line:#d9d9d9;
  --white:#ffffff;
  --head:"Exo 2", sans-serif;
  --body:"Open Sans", sans-serif;
}
*{box-sizing:border-box;margin:0;padding:0}
html,body{width:1200px;height:4157px;overflow:hidden;background:var(--white)}
body{position:relative;font-family:var(--body);color:var(--ink)}
.abs{position:absolute}

/* top bar */
.topbar{left:0;top:0;width:1200px;height:38px;background:var(--yellow);font-size:13px;font-weight:600;color:var(--black)}
.topbar .contact{left:144px;top:10px;display:flex;gap:14px;align-items:center}
.topbar .social{right:145px;top:13px;display:flex;gap:8px}
.topbar .social span{width:12px;height:12px;border-radius:50%;background:var(--black);display:block}

/* hero */
.hero{left:0;top:38px;width:1200px;height:770px;background:radial-gradient(circle at 70% 40%,#3a3a3a 0%,#1a1a1a 45%,#0a0a0a 100%)}
.brand{left:144px;top:88px;display:flex;align-items:center;gap:12px;color:var(--yellow);font-family:var(--head);font-weight:700;font-size:30px;line-height:1}
.brand .mark{width:18px;height:18px;border-radius:50%;background:var(--yellow)}
.nav{left:484px;top:102px;display:flex;gap:30px;align-items:center;font-family:var(--head);font-weight:700;font-size:16px;color:var(--white);letter-spacing:.5px}
.nav .search{width:16px;height:16px}
.hero-title{left:116px;top:292px;font-family:var(--head);font-weight:800;font-size:62px;line-height:66px;color:var(--white);letter-spacing:1px}
.hero-title em{font-style:normal;color:var(--yellow)}
.btn-outline{height:36px;border:1.5px solid var(--white);border-radius:3px;color:var(--white);font-family:var(--head);font-weight:700;font-size:14px;display:flex;align-items:center;justify-content:center;gap:8px;letter-spacing:.5px}
.dots{left:120px;top:627px;display:flex;gap:9px}
.dots span{width:9px;height:9px;border-radius:50%;background:var(--white)}
.dots span.on{background:var(--yellow)}
.showcase{left:640px;top:282px;width:460px;height:460px;border-radius:50%;background:radial-gradient(circle at 45% 45%,#fff48a 0%,var(--yellow) 60%,#e8d92a 100%);box-shadow:0 0 0 12px rgba(0,0,0,.35)}

/* section titles */
.sec-title{left:0;width:1200px;text-align:center;font-family:var(--head);font-weight:700;font-size:38px;color:var(--ink)}
.sec-title em{font-style:normal;color:var(--yellow)}

/* offer cards */
.card{width:280px;height:152px;background:var(--white);border-radius:6px;box-shadow:0 6px 22px rgba(0,0,0,.14)}
.card h3{position:absolute;left:26px;top:58px;font-size:18px;font-weight:700;color:var(--ink)}
.card p{position:absolute;left:26px;top:88px;width:230px;font-size:11.5px;line-height:18px;color:#8a8a8a}
.icon{position:absolute;left:38px;top:-42px;width:80px;height:80px;border-radius:50%;background:var(--yellow);display:flex;align-items:center;justify-content:center;box-shadow:0 4px 10px rgba(0,0,0,.2)}
.icon .in{width:62px;height:62px;border-radius:50%;background:#2b2b2b;display:flex;align-items:center;justify-content:center}

/* about */
.about-photo{left:0;top:1543px;width:600px;height:471px;background:linear-gradient(135deg,#6a5641,#9aa7b6 40%,#d9e3ee 55%,#4b4b4b)}
.about-panel{left:600px;top:1530px;width:600px;height:484px}
.about-head{left:673px;top:1600px;font-family:var(--head);font-weight:700;color:var(--ink);line-height:1.2}
.about-head .a{font-size:36px;color:var(--white);display:block}
.about-head .b{font-size:32px;display:block}
.about-text{left:673px;top:1712px;width:410px;font-size:14px;line-height:26px;color:#3a3a3a}
.btn-dark{left:673px;top:1906px;width:145px;height:37px;border:1.5px solid var(--ink);border-radius:3px;font-family:var(--head);font-weight:700;font-size:13px;display:flex;align-items:center;justify-content:center;gap:8px}

/* testimonials */
.cloud{left:110px;top:2200px;width:980px;height:260px;border-radius:130px;background:linear-gradient(#f7f7f7,#ececec)}
.arrow{top:2305px}
.quote{width:48px;height:48px;border-radius:50%;background:var(--ink);display:flex;align-items:center;justify-content:center;color:var(--yellow);font-family:var(--head);font-size:30px;font-weight:800;line-height:1}
.avatar{width:96px;height:96px;border-radius:50%;background:radial-gradient(circle at 50% 40%,#d9c7b4,#8f7b68);border:4px solid var(--white);box-shadow:0 3px 10px rgba(0,0,0,.2)}
.say{width:320px;font-size:12.5px;line-height:22px;font-style:italic;color:#6a6a6a}
.who{font-family:var(--head);font-weight:700;font-size:21px;color:var(--ink)}

/* blog */
.blog-bg{left:0;top:2470px;width:1200px;height:700px;background:linear-gradient(#f5f5f5,#ececec)}
.post-img{width:280px;height:194px;border:5px solid var(--white);box-shadow:0 4px 14px rgba(0,0,0,.15)}
.post-title{font-size:17px;font-weight:600;color:var(--ink)}
.post-date{font-size:11px;color:#777;display:flex;align-items:center;gap:6px}

/* contact */
.info{display:flex;align-items:center;gap:12px;font-size:13px;line-height:18px;color:var(--grey)}
.info .ic{width:56px;height:56px;border-radius:50%;background:var(--yellow);display:flex;align-items:center;justify-content:center;box-shadow:0 0 0 5px #fff,0 0 0 6px var(--line)}
.field{height:39px;background:var(--white);border:1px solid var(--line);border-radius:4px;font-size:13px;color:#777;padding:11px 14px}
.submit{left:493px;top:3688px;width:211px;height:44px;border-radius:22px;background:var(--yellow);font-family:var(--head);font-weight:700;font-size:16px;color:var(--white);display:flex;align-items:center;justify-content:center;letter-spacing:.5px;box-shadow:0 4px 10px rgba(0,0,0,.12)}

/* footer */
.footer{left:0;top:3850px;width:1200px;height:307px;background:radial-gradient(circle at 50% 30%,#2a2a2a,#0d0d0d 70%)}
.foot-social{left:0;top:3959px;width:1200px;display:flex;justify-content:center;gap:13px}
.foot-social span{width:42px;height:42px;border-radius:50%;border:2px solid var(--white);display:block}
.foot-nav{left:0;top:4036px;width:1200px;text-align:center;font-family:var(--head);font-weight:700;font-size:16px;color:var(--white);word-spacing:4px}
.foot-nav i{font-style:normal;margin:0 14px}
.copy{left:0;top:4084px;width:1200px;text-align:center;font-size:11px;color:#cfcfcf}
</style>
</head>
<body>

<header class="abs topbar">
  <div class="abs contact">
    <span>&#9742; Call 1 800 555 0142</span><span>|</span><span>&#9993; Email : hello@vigilledger.example</span>
  </div>
  <div class="abs social"><span></span><span></span><span></span><span></span></div>
</header>

<section class="abs hero" role="img" aria-label="Dark photograph of a table with soft flowers"></section>
<div class="abs brand"><span class="mark"></span>Vigil Ledger Suite</div>
<nav class="abs nav">
  <span>HOME</span><span>PRESENTATION</span><span>SERVICES</span><span>GALLERY</span><span>CONTACT</span>
  <svg class="search" viewBox="0 0 16 16" fill="none" stroke="#fbee3d" stroke-width="2.4"><circle cx="6.5" cy="6.5" r="4.5"/><path d="M10 10l4.5 4.5"/></svg>
</nav>
<h1 class="abs hero-title">Funeral<br><em>Management</em><br>Software</h1>
<div class="abs btn-outline" style="left:118px;top:535px;width:146px">OUR OFFERS <span>&#10140;</span></div>
<div class="abs btn-outline" style="left:277px;top:535px;width:212px">VIDEO PRESENTATION <span style="color:#fbee3d">&#9679;</span></div>
<div class="abs dots"><span></span><span></span><span class="on"></span><span></span><span></span></div>
<div class="abs showcase" role="img" aria-label="Desktop monitor showing the software with a flower arrangement"></div>

<svg class="abs" style="left:0;top:660px" width="1200" height="160" viewBox="0 0 1200 160">
  <path d="M0 80 C250 150 450 150 650 110 C850 70 1000 40 1200 60 L1200 160 L0 160Z" fill="#5c5c5c"/>
  <path d="M0 95 C250 160 450 160 650 125 C850 85 1000 60 1200 75 L1200 160 L0 160Z" fill="#fbee3d"/>
  <path d="M0 110 C250 170 450 165 650 140 C850 105 1000 85 1200 95 L1200 160 L0 160Z" fill="#ffffff"/>
</svg>

<!-- What we offer -->
<h2 class="abs sec-title" style="top:890px"><em>What</em> we Offer</h2>

<div class="abs card" style="left:144px;top:1045px">
  <div class="icon"><div class="in"><svg width="30" height="30" viewBox="0 0 30 30" fill="#fff"><rect x="3" y="5" width="24" height="15" rx="2"/><rect x="12" y="20" width="6" height="4"/><rect x="8" y="24" width="14" height="2"/></svg></div></div>
  <h3>Online software</h3><p>Lorem Ipsum is simply dummy text of the printing and typesetting industry</p>
</div>
<div class="abs card" style="left:457px;top:1045px">
  <div class="icon"><div class="in"><svg width="30" height="30" viewBox="0 0 30 30" fill="#fff"><path d="M7 3h12l5 5v19H7z"/><g stroke="#2b2b2b" stroke-width="2"><path d="M11 13h9M11 17h9M11 21h9"/></g></svg></div></div>
  <h3>Billing</h3><p>Lorem Ipsum is simply dummy text of the printing and typesetting industry</p>
</div>
<div class="abs card" style="left:773px;top:1045px">
  <div class="icon"><div class="in"><svg width="30" height="30" viewBox="0 0 30 30" fill="#fff"><rect x="4" y="6" width="22" height="6"/><rect x="6" y="13" width="18" height="12"/><rect x="12" y="16" width="6" height="2" fill="#2b2b2b"/></svg></div></div>
  <h3>Archiving</h3><p>Lorem Ipsum is simply dummy text of the printing and typesetting industry</p>
</div>
<div class="abs card" style="left:144px;top:1255px">
  <div class="icon"><div class="in"><svg width="30" height="30" viewBox="0 0 30 30" fill="none" stroke="#fff" stroke-width="2.4"><rect x="5" y="4" width="13" height="17"/><rect x="12" y="9" width="13" height="17" fill="#2b2b2b"/></svg></div></div>
  <h3>Personalized documents</h3><p>Lorem Ipsum is simply dummy text of the printing and typesetting industry</p>
</div>
<div class="abs card" style="left:457px;top:1255px">
  <div class="icon"><div class="in"><svg width="30" height="30" viewBox="0 0 30 30" fill="#fff"><circle cx="15" cy="10" r="5"/><path d="M5 26c0-6 4-9 10-9s10 3 10 9z"/></svg></div></div>
  <h3>Electronic identity card</h3><p>Lorem Ipsum is simply dummy text of the printing and typesetting industry</p>
</div>
<div class="abs card" style="left:773px;top:1255px">
  <div class="icon"><div class="in"><svg width="30" height="30" viewBox="0 0 30 30" fill="#fff"><path d="M15 4c-5 0-8 4-8 9v6l-3 3h22l-3-3v-6c0-5-3-9-8-9z"/><circle cx="15" cy="25" r="3"/></svg></div></div>
  <h3>Notifications</h3><p>Lorem Ipsum is simply dummy text of the printing and typesetting industry</p>
</div>

<!-- About -->
<div class="abs about-photo" role="img" aria-label="Business team around a table with cloud cut-outs"></div>
<svg class="abs about-panel" viewBox="0 0 600 484" preserveAspectRatio="none"><path d="M0 70 C150 0 400 -10 600 20 L600 484 L0 484Z" fill="#fbee3d"/></svg>
<h2 class="abs about-head"><span class="a">About</span><span class="b">Vigil Ledger Suite</span></h2>
<p class="abs about-text">Sed ut perspiciatis unde omnis iste natus error sit voluptatem accusantium doloremque laudantium, totam rem aperiam, eaque ipsa quae ab illo inventore veritatis et quasi architecto beatae vitae dicta sunt explicabo. Nemo enim ipsam voluptatem quia voluptas sit aspernatur aut odit aut fugit, sed quia voluptatem sequi nesciunt.</p>
<div class="abs btn-dark">OUR OFFERS <span>&#10140;</span></div>

<!-- Testimonials -->
<h2 class="abs sec-title" style="top:2133px"><em>Happy</em> customers !!!</h2>
<div class="abs cloud"></div>
<svg class="abs arrow" style="left:78px" width="30" height="56" viewBox="0 0 30 56" fill="none" stroke="#bdbdbd" stroke-width="3"><path d="M26 3L4 28l22 25"/></svg>
<svg class="abs arrow" style="left:1093px" width="30" height="56" viewBox="0 0 30 56" fill="none" stroke="#bdbdbd" stroke-width="3"><path d="M4 3l22 25L4 53"/></svg>

<div class="abs avatar" style="left:140px;top:2292px" role="img" aria-label="Customer portrait"></div>
<div class="abs quote" style="left:166px;top:2255px">&ldquo;</div>
<p class="abs say" style="left:266px;top:2276px">Sed ut perspiciatis unde omnis iste natus error sit voluptatem accusantium doloremque, totam rem aperiam, eaque ipsa quae ab illo inventore veritatis</p>
<div class="abs who" style="left:266px;top:2356px">- Elena R</div>

<div class="abs avatar" style="left:620px;top:2292px" role="img" aria-label="Customer portrait"></div>
<div class="abs quote" style="left:646px;top:2255px">&ldquo;</div>
<p class="abs say" style="left:745px;top:2276px">Sed ut perspiciatis unde omnis iste natus error sit voluptatem accusantium doloremque, totam rem aperiam, eaque ipsa quae ab illo inventore veritatis</p>
<div class="abs who" style="left:745px;top:2356px">- Elena R</div>

<!-- Blog -->
<div class="abs blog-bg"></div>
<svg class="abs" style="left:0;top:2460px" width="1200" height="120" viewBox="0 0 1200 120">
  <path d="M0 0 H1200 V40 C900 -10 500 110 0 50Z" fill="#ffffff"/>
  <path d="M0 50 C200 60 320 80 420 110 C300 95 150 80 0 72Z" fill="#1e1e1e"/>
  <path d="M0 72 C150 80 300 95 420 110 C280 100 150 92 0 90Z" fill="#fbee3d"/>
</svg>
<h2 class="abs sec-title" style="top:2643px"><em>Blog</em> Posts</h2>

<div class="abs post-img" style="left:144px;top:2751px;background:linear-gradient(135deg,#2f8fa8,#d9b24a 50%,#c74c3d)" role="img" aria-label="Desk with laptop and office supplies"></div>
<div class="abs post-title" style="left:144px;top:2958px">Sed ut perspiciatis unde omnis</div>
<div class="abs post-date" style="left:146px;top:2993px"><svg width="11" height="11" viewBox="0 0 11 11" fill="none" stroke="#d6c800" stroke-width="1.4"><rect x="1" y="2" width="9" height="8"/><path d="M1 5h9"/></svg>Apr 19,2019</div>

<div class="abs post-img" style="left:460px;top:2751px;background:linear-gradient(135deg,#3e5a2f,#8d7a5e 50%,#2a2a2a)" role="img" aria-label="Two people holding hands"></div>
<div class="abs post-title" style="left:460px;top:2958px">Sed ut perspiciatis unde omnis</div>
<div class="abs post-date" style="left:462px;top:2993px"><svg width="11" height="11" viewBox="0 0 11 11" fill="none" stroke="#d6c800" stroke-width="1.4"><rect x="1" y="2" width="9" height="8"/><path d="M1 5h9"/></svg>Apr 19,2019</div>

<div class="abs post-img" style="left:776px;top:2751px;background:linear-gradient(135deg,#6c7a86,#c9c4bd 55%,#d58fa6)" role="img" aria-label="Stone angel statue with pink flowers"></div>
<div class="abs post-title" style="left:776px;top:2958px">Sed ut perspiciatis unde omnis</div>
<div class="abs post-date" style="left:778px;top:2993px"><svg width="11" height="11" viewBox="0 0 11 11" fill="none" stroke="#d6c800" stroke-width="1.4"><rect x="1" y="2" width="9" height="8"/><path d="M1 5h9"/></svg>Apr 19,2019</div>

<svg class="abs" style="left:0;top:3050px" width="1200" height="140" viewBox="0 0 1200 140">
  <path d="M700 40 C900 60 1080 70 1200 50 V72 C1050 100 880 80 700 40Z" fill="#1e1e1e"/>
  <path d="M760 60 C950 90 1100 95 1200 78 V92 C1100 112 950 105 760 60Z" fill="#fbee3d"/>
  <path d="M0 80 C400 150 800 150 1200 95 V140 H0Z" fill="#ffffff"/>
</svg>

<!-- Contact -->
<h2 class="abs sec-title" style="top:3258px"><em>Contact</em> Us</h2>
<div class="abs info" style="left:213px;top:3358px">
  <div class="ic"><svg width="22" height="26" viewBox="0 0 22 26" fill="#fff"><path d="M11 1C5.5 1 2 5 2 10c0 6 9 15 9 15s9-9 9-15c0-5-3.5-9-9-9z"/><circle cx="11" cy="10" r="3.5" fill="#fbee3d"/></svg></div>
  <div>234,Sed ut perspiciatis unde<br>omnis iste natus...</div>
</div>
<div class="abs info" style="left:521px;top:3358px">
  <div class="ic"><svg width="24" height="24" viewBox="0 0 24 24" fill="#fff"><path d="M5 2l4 1 2 5-3 2c1 3 3 5 6 6l2-3 5 2 1 4c-1 2-3 3-5 3C10 22 2 14 2 7c0-2 1-4 3-5z"/></svg></div>
  <div>Call Us<br>1 800 555 0142</div>
</div>
<div class="abs info" style="left:759px;top:3358px">
  <div class="ic"><svg width="26" height="20" viewBox="0 0 26 20" fill="#fff"><rect x="1" y="1" width="24" height="18" rx="2"/><path d="M2 3l11 8 11-8" fill="none" stroke="#fbee3d" stroke-width="2"/></svg></div>
  <div>Email<br>hello@vigilledger.example</div>
</div>

<div class="abs field" style="left:255px;top:3458px;width:332px">Enter Name</div>
<div class="abs field" style="left:612px;top:3458px;width:333px">Enter Email</div>
<div class="abs field" style="left:255px;top:3519px;width:332px">Phone</div>
<div class="abs field" style="left:612px;top:3519px;width:333px">Subject</div>
<div class="abs field" style="left:255px;top:3580px;width:690px;height:72px">Message</div>
<div class="abs submit">SUBMIT MESSAGE</div>

<!-- Footer -->
<div class="abs footer"></div>
<svg class="abs" style="left:0;top:3780px" width="1200" height="110" viewBox="0 0 1200 110">
  <path d="M0 40 C300 95 800 100 1200 30 V110 H0Z" fill="#fbee3d"/>
  <path d="M0 62 C300 110 800 112 1200 50 V110 H0Z" fill="#5c5c5c"/>
  <path d="M0 75 C300 120 800 120 1200 68 V110 H0Z" fill="#111111"/>
</svg>
<div class="abs foot-social"><span></span><span></span><span></span><span></span><span></span></div>
<nav class="abs foot-nav">HOME<i>/</i>PRESENTATION<i>/</i>SERVICES<i>/</i>GALLERY<i>/</i>CONTACT</nav>
<p class="abs copy">Copyright © 2019 Vigil Ledger Suite All right reserved &nbsp;|&nbsp; Privacy policy</p>

</body>
</html>
```